CLAIMGUARD LEGAL

I'm virtually ready to launch my site, but I have a number of edits and modifications that need to be implemented. More importantly, I'm always looking to improve my site, particularly now that I am making my proverbial "FIRST IMPRESSION." Thus, I'm willing to see if there is someone who can add creativity and perhaps improve what I already have, particularly on the All Important Front Page.

```html
<!DOCTYPE html>
<html lang="en">
<head>
<meta charset="utf-8">
<title>Claimguard Legal</title>
<link href="https://fonts.googleapis.com/css2?family=Ubuntu:wght@400;500;700&family=Lato:wght@400;700;900&display=swap" rel="stylesheet">
<style>
:root{
  --navy:#1c2a59;
  --navy-dark:#14204a;
  --red:#b3121c;
  --red-bright:#d9232d;
  --light:#f1f3f8;
  --text:#2b2f3a;
  --muted:#8a8f9c;
  --white:#ffffff;
}
*{box-sizing:border-box;margin:0;padding:0}
html,body{width:1200px;height:4726px;overflow:hidden}
body{position:relative;background:var(--white);font-family:"Lato",sans-serif;color:var(--text)}
.abs{position:absolute}
.h{font-family:"Ubuntu",sans-serif;color:var(--navy)}
.center{text-align:center}
.eyebrow{font-size:13px;color:var(--red);font-weight:700;letter-spacing:.3px;text-transform:uppercase}
.photo{position:absolute}
.brand{display:flex;align-items:center;gap:8px;font-family:"Ubuntu",sans-serif;font-weight:700;color:var(--navy);font-size:15px}
.brand i{display:block;width:34px;height:34px;border-radius:50%;background:var(--red)}

/* top bar */
.topbar{left:385px;top:0;width:815px;height:31px;background:var(--navy);display:flex;align-items:center;gap:60px;padding-left:60px;color:#fff;font-size:11px;font-weight:700}
.topbar .appt{background:var(--red);height:31px;padding:0 30px;display:flex;align-items:center}
.nav{top:58px;left:398px;display:flex;gap:30px;font-size:11px;color:var(--text)}
.btn-outline{border:1.5px solid var(--navy);color:var(--navy);font-size:11px;font-weight:700;display:flex;align-items:center;justify-content:center;border-radius:3px}

/* hero */
.hero{left:0;top:100px;width:1200px;height:618px;background:linear-gradient(100deg,#2d3648 0%,#4a5266 40%,#6f6e74 60%,#3a4157 100%)}
.hero::after{content:"";position:absolute;inset:0;background:rgba(20,32,74,.45)}
.welcome{left:516px;top:299px;width:165px;height:37px;background:var(--navy);color:#fff;font-size:11px;font-weight:700;display:flex;align-items:center;justify-content:center;z-index:2}
.hero-title{left:0;top:350px;width:1200px;color:#fff;font-size:62px;font-weight:700;line-height:74px;z-index:2;font-family:"Ubuntu",sans-serif}
.hero-btn{left:516px;top:517px;width:165px;height:48px;border:1.5px solid #fff;color:#fff;font-size:11px;font-weight:700;display:flex;align-items:center;justify-content:center;z-index:2}

/* about */
.about-text p{font-size:12.5px;line-height:22px;color:var(--muted)}
.btn-red{background:var(--red);color:#fff;font-weight:700;font-size:15px;display:flex;align-items:center;justify-content:center;gap:12px;border-radius:3px}

/* services */
.services{left:0;top:1318px;width:1200px;height:653px;background:var(--light)}
.svc-label{width:275px;height:95px;background:#fff;box-shadow:0 6px 18px rgba(0,0,0,.08);display:flex;align-items:center;justify-content:center;font-family:"Ubuntu",sans-serif;font-size:19px;color:var(--navy)}
.svc-icon{width:88px;height:88px;border-radius:50%;background:var(--navy);display:flex;align-items:center;justify-content:center}
.svc-ring{width:110px;height:110px;border-radius:50%;border:2px solid var(--red);border-bottom-color:transparent;border-left-color:transparent;transform:rotate(-45deg)}

/* call band */
.call{left:0;top:1971px;width:1200px;height:308px;background:linear-gradient(90deg,#1c2a59 0%,#3b4768 50%,#1c2a59 100%)}
.call-title{left:0;top:2078px;width:1200px;color:#fff;font-family:"Ubuntu",sans-serif;font-size:34px;line-height:42px;font-weight:500}
.call-pill{left:350px;top:2246px;width:501px;height:55px;background:#fff;border-radius:4px;display:flex;align-items:center;justify-content:space-around;font-size:16px;color:var(--navy)}

/* why */
.why-card{width:235px;height:264px;background:#fff;box-shadow:0 4px 16px rgba(0,0,0,.08);text-align:center;padding-top:30px}
.why-card .ic{width:84px;height:84px;border-radius:50%;background:#f4f4f6;margin:0 auto;display:flex;align-items:center;justify-content:center}
.why-card h3{font-family:"Ubuntu",sans-serif;font-weight:500;font-size:21px;color:var(--navy);margin-top:22px}
.why-card p{font-size:13px;line-height:18px;color:var(--muted);margin:14px 24px 0}
.why-card.active{background:var(--navy)}
.why-card.active h3,.why-card.active p{color:#fff}
.why-card.active .ic{background:#fff}

/* testimonials */
.testi-band{left:0;top:3070px;width:1200px;height:358px;background:linear-gradient(90deg,#2a3d72,#3a5087 60%,#2a3d72)}
.t-card{width:301px;height:327px;background:#fff;box-shadow:0 6px 20px rgba(0,0,0,.08);padding:45px 40px 0 42px}
.t-card .stars{color:#e0621b;font-size:17px;letter-spacing:7px}
.t-card p{font-size:13px;line-height:18.5px;color:var(--muted);margin-top:12px}
.t-card hr{border:0;border-top:1px solid #cfd2d8;margin:30px 0 22px}
.t-person{display:flex;align-items:center;gap:14px}
.t-person i{display:block;width:58px;height:58px;border-radius:50%;background:linear-gradient(135deg,#e9d3c4,#b98c78)}
.t-person b{display:block;font-size:15px;color:#555}
.t-person span{font-size:13px;color:var(--muted)}
.quote{width:52px;height:52px;border-radius:50%;background:#1b9bd1;color:#fff;font-family:"Ubuntu",sans-serif;font-weight:700;font-size:34px;display:flex;align-items:center;justify-content:center;line-height:1}

/* contact */
.contact-card{left:138px;top:3868px;width:923px;height:459px;background:#fff;border-radius:22px;box-shadow:0 10px 30px rgba(0,0,0,.12);overflow:hidden;z-index:2}
.field{position:absolute;border:1px solid #c9ccd3;border-radius:3px;font-size:11px;color:#777;padding:8px 8px}
.send{position:absolute;background:var(--red);color:#fff;font-weight:700;font-size:13px;display:flex;align-items:center;justify-content:center;border-radius:3px}

/* footer */
.footer-nav{left:0;top:4490px;width:1200px;display:flex;justify-content:center;gap:46px;color:#fff;font-weight:700;font-size:14px;font-family:"Ubuntu",sans-serif}
.f-item{display:flex;align-items:center;gap:14px;color:#fff;font-size:12px;line-height:17px}
.f-item .ring{width:56px;height:56px;border-radius:50%;border:1.5px solid #fff;display:flex;align-items:center;justify-content:center}
.bottom{left:0;top:4676px;width:1200px;height:50px;background:#2b3578;color:#fff;font-size:12px;font-weight:700}
.social{display:flex;gap:6px}
.social span{display:block;width:25px;height:25px;border:1.5px solid #fff;border-radius:3px}
</style>
</head>
<body>

<!-- header -->
<div class="abs brand" style="left:212px;top:38px"><i></i>Claimguard Legal</div>
<div class="abs topbar">
  <span>&#9742;&nbsp; 555 - 210 - 4460</span>
  <span class="appt">&#9993;&nbsp; REQUEST AN APPOINTMENT</span>
  <span>&#9679;&nbsp; 1234 Some Place Somewhere</span>
</div>
<nav class="abs nav" style="top:62px"><span>Home</span><span>About Us</span><span>Services</span><span>Our Team</span><span>Blog</span></nav>
<div class="abs btn-outline" style="left:932px;top:55px;width:118px;height:30px">CONTACT US</div>

<!-- hero -->
<div class="abs hero" role="img" aria-label="Team of lawyers meeting in a bright office"></div>
<div class="abs welcome">WELCOME</div>
<h1 class="abs hero-title center">Legal Precision,<br>Client Success</h1>
<div class="abs hero-btn">ABOUT COMPANY</div>

<!-- about -->
<div class="photo" style="left:90px;top:857px;width:246px;height:365px;background:linear-gradient(160deg,#5c5f68,#2e3038)" role="img" aria-label="Lawyer reviewing a document"></div>
<div class="photo" style="left:350px;top:811px;width:226px;height:222px;background:linear-gradient(160deg,#8b8f98,#3a3e48)" role="img" aria-label="Colleagues discussing a case"></div>
<div class="photo" style="left:350px;top:1046px;width:226px;height:222px;background:linear-gradient(160deg,#b08a60,#5b4530)" role="img" aria-label="Scales of justice and gavel on a desk"></div>
<div class="abs" style="left:297px;top:990px;width:100px;height:100px;border-radius:50%;background:#fff;display:flex;align-items:center;justify-content:center"><span style="width:50px;height:50px;border-radius:50%;background:var(--red);display:block"></span></div>
<div class="abs about-text" style="left:624px;top:838px;width:510px">
  <div class="eyebrow">Who we are</div>
  <h2 class="h" style="font-size:41px;line-height:53px;font-weight:500;margin-top:22px">The team you can trust<br>to get the job done</h2>
  <div class="h" style="font-size:22px;margin-top:22px">Turning Challenges into Legal Triumphs</div>
  <p style="margin-top:18px">Lorem ipsum dolor sit amet, consectetur adipiscing elit, sed do eiusmod tempor incididunt ut labore et dolore magna aliqua. Ut enim ad minim veniam, quis nos trud exercitation ullamco laboris nisi ut aliquip ex ea commodo consequat. Duis aute irure dolor in reprehenderit in voluptate velit esse cillum dolore eu fugiat nulla pariatur. Excepteur sint occaecat cupidatat non proident, sunt in culpa qui officia deserunt mollit anim id est laborum.</p>
</div>
<div class="abs btn-red" style="left:624px;top:1205px;width:154px;height:45px">Contact us <span>&rarr;</span></div>

<!-- services -->
<div class="abs services"></div>
<div class="abs eyebrow center" style="left:0;top:1398px;width:1200px">Our services</div>
<h2 class="abs h center" style="left:0;top:1433px;width:1200px;font-size:40px;font-weight:500">Services We Offer</h2>

<div class="photo" style="left:90px;top:1596px;width:325px;height:263px;background:linear-gradient(135deg,#2c4a7a,#6f8fb8)" role="img" aria-label="Legal consultation concept"></div>
<div class="photo" style="left:440px;top:1596px;width:325px;height:263px;background:linear-gradient(135deg,#3b2a18,#8a6a40)" role="img" aria-label="Judge gavel in a courtroom"></div>
<div class="photo" style="left:791px;top:1596px;width:326px;height:263px;background:linear-gradient(135deg,#2e3a52,#7d8aa3)" role="img" aria-label="Person signing collection paperwork"></div>

<div class="abs svc-ring" style="left:198px;top:1541px"></div>
<div class="abs svc-icon" style="left:209px;top:1552px"><svg width="36" height="36" viewBox="0 0 36 36" fill="#fff"><g><circle cx="18" cy="4" r="3"/><circle cx="28" cy="8" r="2.6"/><circle cx="32" cy="18" r="2.4"/><circle cx="28" cy="28" r="2.2"/><circle cx="18" cy="32" r="2"/><circle cx="8" cy="28" r="1.8"/><circle cx="4" cy="18" r="1.6"/><circle cx="8" cy="8" r="1.4"/></g></svg></div>
<div class="abs svc-ring" style="left:548px;top:1541px"></div>
<div class="abs svc-icon" style="left:559px;top:1552px"><svg width="34" height="38" viewBox="0 0 34 38" fill="none" stroke="#fff" stroke-width="2.4" stroke-linecap="round"><path d="M14 20V8a3 3 0 0 1 6 0v10l6 1c3 1 4 3 3 6l-2 8H14l-5-8c-1-2 1-4 3-3l2 2"/><path d="M8 10a9 9 0 0 1 18 0"/></svg></div>
<div class="abs svc-ring" style="left:899px;top:1541px"></div>
<div class="abs svc-icon" style="left:910px;top:1552px"><svg width="38" height="38" viewBox="0 0 38 38" fill="none" stroke="#fff" stroke-width="2.6" stroke-linecap="round"><path d="M19 3v10M15 9l4 4 4-4M19 35V25M15 29l4-4 4 4M3 19h10M9 15l4 4-4 4M35 19H25M29 15l-4 4 4 4"/></svg></div>

<div class="abs svc-label" style="left:116px;top:1813px">Consultation</div>
<div class="abs svc-label" style="left:466px;top:1813px">Litigation</div>
<div class="abs svc-label" style="left:817px;top:1813px">Collection Claims</div>

<!-- call band -->
<div class="abs call" role="img" aria-label="Attorneys working together in an office, darkened"></div>
<div class="abs call-title center">We're on Call <span style="color:var(--red-bright)">24/7</span> t React Promptly to Your<br>Legal Needs</div>
<div class="abs call-pill"><span>+ (001) 234-567-890</span><span>[or]</span><span>info@example.com</span></div>

<!-- why choose us -->
<div class="photo" style="left:760px;top:2279px;width:440px;height:791px;background:linear-gradient(90deg,#ffffff 0%,#d7dbe3 30%,#a9b2c2 70%,#c6ccd7 100%)" role="img" aria-label="Smiling professional woman with arms crossed in an office"></div>
<div class="abs eyebrow center" style="left:0;top:2338px;width:1188px;font-size:11px">Why choose us</div>
<h2 class="abs h center" style="left:0;top:2372px;width:1200px;font-size:40px;font-weight:500">Why Choose Us</h2>

<div class="abs why-card" style="left:97px;top:2470px"><div class="ic"><svg width="40" height="40" viewBox="0 0 40 40" fill="none" stroke="#b3121c" stroke-width="3"><path d="M10 20v-6a10 10 0 0 1 20 0v6"/><rect x="8" y="20" width="24" height="12" rx="6"/><path d="M26 26h-8"/></svg></div><h3>Client Centric</h3><p>Lorem ipsum dolor sit amet, consectetur adipiscing elit, sed do eiusmod tem</p></div>
<div class="abs why-card active" style="left:354px;top:2470px"><div class="ic" style="background:#fff"><svg width="64" height="64" viewBox="0 0 64 64" fill="none" stroke="#b3121c" stroke-width="4"><circle cx="32" cy="32" r="30" fill="#b3121c" stroke="none"/><circle cx="32" cy="32" r="18" stroke="#fff"/><circle cx="32" cy="32" r="9" stroke="#fff"/></svg></div><h3>Free Consultation</h3><p>Lorem ipsum dolor sit amet, consectetur adipiscing elit, sed do eiusmod tem</p></div>
<div class="abs why-card" style="left:609px;top:2470px"><div class="ic"><svg width="40" height="40" viewBox="0 0 40 40" fill="none" stroke="#b3121c" stroke-width="3" stroke-linecap="round"><circle cx="20" cy="8" r="4"/><path d="M6 16l14 4 14-4M20 20v6M12 36l8-10 8 10"/></svg></div><h3>Minimize Exposure</h3><p>Lorem ipsum dolor sit amet, consectetur adipiscing elit, sed do eiusmod tem</p></div>
<div class="abs why-card" style="left:97px;top:2756px"><div class="ic"><svg width="44" height="40" viewBox="0 0 44 40" fill="none" stroke="#b3121c" stroke-width="3" stroke-linecap="round"><circle cx="12" cy="12" r="5"/><path d="M3 30a9 9 0 0 1 18 0H3zM26 10h14M26 18h14M24 26h16"/></svg></div><h3>Attorney Letters</h3><p>Lorem ipsum dolor sit amet, consectetur adipiscing elit, sed do eiusmod tem</p></div>
<div class="abs why-card" style="left:354px;top:2756px"><div class="ic"><svg width="40" height="40" viewBox="0 0 40 40" fill="#b3121c"><rect x="6" y="26" width="5" height="10"/><rect x="14" y="20" width="5" height="16"/><rect x="22" y="22" width="5" height="14"/><rect x="30" y="14" width="5" height="22"/><circle cx="32" cy="7" r="3"/></svg></div><h3>Affordable</h3><p>Lorem ipsum dolor sit amet, consectetur adipiscing elit, sed do eiusmod tem</p></div>
<div class="abs why-card" style="left:609px;top:2756px"><div class="ic"><svg width="40" height="40" viewBox="0 0 40 40" fill="none" stroke="#b3121c" stroke-width="3"><rect x="4" y="4" width="10" height="10"/><rect x="26" y="4" width="10" height="10"/><rect x="4" y="26" width="10" height="10"/><rect x="26" y="26" width="10" height="10"/><path d="M14 9h12M9 14v12M31 14v12"/></svg></div><h3>Legal Experts</h3><p>Lorem ipsum dolor sit amet, consectetur adipiscing elit, sed do eiusmod tem</p></div>

<!-- testimonials -->
<div class="abs testi-band" role="img" aria-label="Office team in discussion, tinted blue"></div>
<div class="abs center" style="left:0;top:3162px;width:1190px;color:#fff;font-size:13px;font-weight:700"><span style="border-bottom:1.5px solid #fff;padding-bottom:3px">TESTIMONIALS</span></div>
<h2 class="abs center" style="left:0;top:3198px;width:1200px;color:#fff;font-family:'Ubuntu',sans-serif;font-size:40px;font-weight:700">Our Testimonials</h2>

<div class="abs t-card" style="left:110px;top:3308px"><div class="stars">★★★★★</div><p>Lorem ipsum dolor sit amet, consectetur adipiscing elit, sed do eiusmod tempor incididunt ut labore et dolore magna aliqua. Ut enim ad minim veniam, q</p><hr><div class="t-person"><i role="img" aria-label="Client portrait"></i><div><b>Mara Ellison</b><span>Human Resource</span></div></div></div>
<div class="abs t-card" style="left:461px;top:3308px"><div class="stars">★★★★★</div><p>Lorem ipsum dolor sit amet, consectetur adipiscing elit, sed do eiusmod tempor incididunt ut labore et dolore magna aliqua. Ut enim ad minim veniam, q</p><hr><div class="t-person"><i role="img" aria-label="Client portrait"></i><div><b>Mara Ellison</b><span>Human Resource</span></div></div></div>
<div class="abs t-card" style="left:806px;top:3308px"><div class="stars">★★★★★</div><p>Lorem ipsum dolor sit amet, consectetur adipiscing elit, sed do eiusmod tempor incididunt ut labore et dolore magna aliqua. Ut enim ad minim veniam, q</p><hr><div class="t-person"><i role="img" aria-label="Client portrait"></i><div><b>Mara Ellison</b><span>Human Resource</span></div></div></div>
<div class="abs quote" style="left:84px;top:3345px">&ldquo;</div>
<div class="abs quote" style="left:435px;top:3345px">&ldquo;</div>
<div class="abs quote" style="left:780px;top:3345px">&ldquo;</div>

<!-- contact -->
<div class="abs eyebrow center" style="left:0;top:3718px;width:1190px;font-size:12px"><span style="border-bottom:1.5px solid var(--red);padding-bottom:3px">Contact us</span></div>
<h2 class="abs h center" style="left:0;top:3752px;width:1200px;font-size:40px;font-weight:500">Get in touch with us</h2>

<svg class="abs" style="left:0;top:4120px;z-index:1" width="1200" height="606" viewBox="0 0 1200 606">
  <path d="M0 130 Q300 90 600 150 T1200 110 V606 H0Z" fill="var(--navy-dark)"/>
  <path d="M0 150 Q110 40 240 10 L240 40 Q110 80 0 190Z" fill="var(--red)"/>
  <path d="M1200 190 Q1090 80 960 30 L960 0 Q1100 40 1200 140Z" fill="var(--red)"/>
</svg>

<div class="abs contact-card">
  <div class="photo" style="left:0;top:0;width:462px;height:459px;background:linear-gradient(135deg,#c9ced6,#6c7584)" role="img" aria-label="Two businessmen reviewing a tablet"></div>
  <span class="abs" style="left:520px;top:51px;width:60px;height:60px;border-radius:50%;background:var(--red);display:block"></span>
  <div class="abs h" style="left:511px;top:113px;font-size:28px;font-weight:400">Please fill out the form</div>
  <div class="field" style="left:512px;top:173px;width:359px;height:37px">Name</div>
  <div class="field" style="left:512px;top:226px;width:173px;height:37px">Phone</div>
  <div class="field" style="left:698px;top:226px;width:173px;height:37px">Email</div>
  <div class="field" style="left:512px;top:279px;width:359px;height:68px">Message</div>
  <div class="send" style="left:512px;top:365px;width:359px;height:35px">Send</div>
</div>

<!-- footer -->
<div class="abs brand center" style="left:0;top:4405px;width:1200px;justify-content:center;color:#fff;font-size:17px;z-index:2"><i></i>Claimguard Legal</div>
<nav class="abs footer-nav" style="z-index:2"><span>HOME</span><span>SERVICES</span><span>ABOUT US</span><span>TESTIMONIALS</span><span>BLOG</span></nav>
<div class="abs" style="left:140px;top:4538px;width:920px;border-top:1px solid rgba(255,255,255,.5);z-index:2"></div>
<div class="abs" style="left:430px;top:4570px;height:70px;border-left:1px solid rgba(255,255,255,.6);z-index:2"></div>
<div class="abs" style="left:750px;top:4570px;height:70px;border-left:1px solid rgba(255,255,255,.6);z-index:2"></div>
<div class="abs f-item" style="left:172px;top:4583px;z-index:2"><div class="ring"><svg width="28" height="28" viewBox="0 0 28 28" fill="none" stroke="#fff" stroke-width="1.6"><circle cx="14" cy="14" r="11"/><path d="M3 14h22M14 3c-5 6-5 16 0 22M14 3c5 6 5 16 0 22"/></svg></div><div style="font-weight:700">123, Building Name, Street<br>City, State XY 123456</div></div>
<div class="abs f-item" style="left:505px;top:4583px;z-index:2"><div class="ring"><svg width="20" height="28" viewBox="0 0 20 28" fill="none" stroke="#fff" stroke-width="1.8"><rect x="3" y="2" width="14" height="24" rx="3"/><path d="M8 22h4"/></svg></div><div><b style="font-size:14px">PHONE</b><br>(123) 456 7890</div></div>
<div class="abs f-item" style="left:827px;top:4583px;z-index:2"><div class="ring"><svg width="28" height="24" viewBox="0 0 28 24" fill="none" stroke="#fff" stroke-width="1.8"><rect x="2" y="3" width="24" height="18" rx="2"/><path d="M2 5l12 9 12-9"/></svg></div><div><b style="font-size:14px">EMAIL</b><br>info@company.com</div></div>

<div class="abs bottom" style="z-index:2;display:flex;align-items:center;justify-content:space-between;padding:0 140px 0 147px">
  <span>Claimguard Legal</span>
  <div class="social"><span></span><span></span><span></span><span></span></div>
</div>

</body>
</html>
```